Wed site for biomedical device startup

We need a generic website for a medical device startup. I will provide examples below of websites from other companies that can serve as models for what we are looking for. The startup is for a device that can non invasively measure blood flow in the brain using light. The application is to detect the type of stroke someone is having before they get to the hospital so treatment can be started right away. This saves patients upto hours of delayed treatment. Patients will be able to recover from stroke much better and faster as a result. I have attached an AI generated illustration of what the device will ultimately look like for reference.

https://www.372clinicaltech.com
https://vextalune.com

Target Market(s)

Biomedical, medical device, investors of biomedical device startups

Industry/Entity Type

Biomedical

Coding

Coded - Design and coding required

Number of Pages Required

4 page

Requirements
Must have
• same section and section headings as example websites listed above
Nice to have
• similar to example websites listed above. Prefer a darker website over a lighter one. Perhaps dark blues to go with logo colors. A moving background image element at top of landing page could be cool. Something indicative of heartbeat, or neurons, or blood flow.

```html
<!DOCTYPE html>
<html lang="en">
<head>
<meta charset="utf-8">
<title>LUMORA – Breakthrough Biomedical Technology</title>
<link href="https://fonts.googleapis.com/css2?family=Lexend:wght@300;400;500;600&display=swap" rel="stylesheet">
<style>
  :root {
    --navy: #0b0a48;
    --navy-deep: #080735;
    --panel: #0e0d55;
    --line: #2a2a85;
    --cyan: #1ec8e0;
    --purple: #a43ad8;
    --white: #ffffff;
    --muted: #d8dbf5;
    --card-cyan: #13d3e8;
  }
  * { box-sizing: border-box; margin: 0; padding: 0; }
  html, body { width: 1200px; height: 3795px; overflow: hidden; }
  body {
    background: var(--navy);
    font-family: "Lexend", sans-serif;
    color: var(--white);
    position: relative;
  }
  .abs { position: absolute; }
  .brand { display: flex; align-items: center; gap: 14px; }
  .brand-dot { width: 50px; height: 50px; border-radius: 50%; background: linear-gradient(135deg, var(--cyan), var(--purple)); }
  .brand-name { font-size: 38px; font-weight: 300; letter-spacing: 3px; color: var(--white); }

  .nav { top: 61px; left: 594px; display: flex; gap: 31px; font-size: 12.5px; font-weight: 500; }
  .nav a { color: var(--white); text-decoration: none; }
  .nav a.active { color: var(--cyan); }
  .search { left: 1055px; top: 53px; width: 32px; height: 32px; border: 1.5px solid var(--cyan); border-radius: 50%; display: flex; align-items: center; justify-content: center; }

  .eyebrow { left: 110px; top: 152px; font-size: 12.5px; font-weight: 500; }
  .hero-title { left: 110px; top: 198px; font-size: 21px; font-weight: 600; line-height: 44px; color: var(--cyan); background: linear-gradient(90deg, var(--cyan) 40%, var(--purple)); -webkit-background-clip: text; background-clip: text; -webkit-text-fill-color: transparent; }
  .hero-copy { left: 680px; top: 131px; width: 420px; font-size: 13px; line-height: 33px; font-weight: 300; }

  .btn { display: flex; align-items: center; justify-content: center; height: 40px; border-radius: 20px; font-size: 12.5px; font-weight: 500; color: var(--white); }
  .btn-ghost { background: var(--navy-deep); border: 1px solid var(--line); }
  .btn-grad { background: linear-gradient(90deg, var(--cyan), var(--purple)); }
  .btn-grad.dark-text { color: var(--navy); }

  .hero-media { left: 106px; top: 351px; width: 986px; height: 429px; border-radius: 14px; background: linear-gradient(120deg, #0f6f90 0%, #1a3fb0 35%, #3b2ab8 60%, #7a1fc4 100%); }

  .section-title { left: 0; width: 1200px; text-align: center; font-size: 27px; font-weight: 600; color: var(--cyan); }
  .section-title span { color: var(--purple); }

  .icon-ring { width: 64px; height: 64px; border-radius: 50%; border: 1.5px solid #3d3db0; background: var(--navy-deep); display: flex; align-items: center; justify-content: center; }
  .feature { width: 290px; }
  .feature h3 { font-size: 14.5px; font-weight: 500; color: var(--cyan); margin-top: 44px; }
  .feature p { font-size: 14px; font-weight: 300; line-height: 34px; margin-top: 21px; }

  .about-box { left: 110px; top: 1352px; width: 978px; height: 575px; border: 1px solid var(--line); border-radius: 0 28px 0 0; background: linear-gradient(120deg, #0d0c52, #100e5c 60%, #0c0b4e); }
  .about-title { left: 170px; top: 1424px; font-size: 27px; font-weight: 600; color: var(--cyan); }
  .about-title span { color: var(--purple); }
  .about-copy { left: 170px; top: 1488px; width: 370px; font-size: 13.5px; font-weight: 300; line-height: 33.5px; }
  .about-copy p + p { margin-top: 18px; }
  .about-media { left: 582px; top: 1421px; width: 436px; height: 436px; border-radius: 50%; background: radial-gradient(circle at 45% 45%, #3fe0ef 0%, #17a9c4 45%, #0b4c6d 80%); border-bottom: 4px solid var(--purple); }

  .why-item { text-align: center; left: 350px; width: 500px; }
  .why-item h3, .side-item h3 { font-size: 13.5px; font-weight: 500; color: var(--cyan); }
  .why-item p, .side-item p { font-size: 14px; font-weight: 300; line-height: 33.5px; margin-top: 20px; }
  .side-item { width: 245px; }
  .side-item.left { left: 104px; text-align: right; }
  .side-item.right { left: 852px; text-align: left; }
  .orbit { left: 420px; top: 2255px; width: 360px; height: 360px; border-radius: 50%; border: 1px solid #1f1f78; }
  .core { left: 505px; top: 2340px; width: 190px; height: 190px; border-radius: 50%; background: linear-gradient(160deg, var(--cyan), #4b5bd8 55%, var(--purple)); }
  .node { width: 66px; height: 66px; border-radius: 50%; border: 1.5px dashed #3d3db0; background: var(--navy); display: flex; align-items: center; justify-content: center; }

  .card { top: 2944px; width: 308px; height: 401px; border: 1px solid #1c1b6a; border-radius: 6px; background: var(--navy); overflow: hidden; }
  .card .media { position: absolute; left: 13px; top: 16px; width: 282px; height: 191px; border-radius: 4px; }
  .card .date { position: absolute; left: 29px; top: 245px; font-size: 12.5px; font-weight: 500; }
  .card h3 { position: absolute; left: 29px; top: 282px; font-size: 16px; font-weight: 500; color: var(--cyan); }
  .card p { position: absolute; left: 29px; top: 314px; width: 250px; font-size: 14px; font-weight: 300; line-height: 34px; }
  .card.featured { background: var(--card-cyan); border-color: var(--card-cyan); }
  .card.featured h3, .card.featured .date, .card.featured p { color: var(--navy); }
  .card .corner { position: absolute; right: -1px; bottom: -1px; width: 50px; height: 40px; border-radius: 40px 0 0 0; background: var(--purple); display: flex; align-items: center; justify-content: center; padding: 6px 0 0 8px; }

  .footer { left: 0; top: 3523px; width: 1200px; height: 272px; background: var(--navy-deep); }
  .footer-brand { left: 0; width: 1200px; top: 3573px; justify-content: center; }
  .footer-nav { left: 0; width: 1200px; top: 3678px; display: flex; justify-content: center; gap: 22px; font-size: 13px; font-weight: 500; }
  .footer-nav .sep { color: var(--muted); }
  .copyright { left: 0; width: 1200px; top: 3732px; text-align: center; font-size: 12.5px; font-weight: 500; }
  .copyright span { color: var(--cyan); }
</style>
</head>
<body>

<header>
  <div class="abs brand" style="left:110px; top:40px;">
    <div class="brand-dot"></div>
    <div class="brand-name">LUMORA</div>
  </div>
  <nav class="abs nav">
    <a class="active" href="#">HOME</a>
    <a href="#">ABOUT</a>
    <a href="#">TECHNOLOGY</a>
    <a href="#">PRESS</a>
    <a href="#">CONTACT</a>
  </nav>
  <div class="abs search">
    <svg width="12" height="12" viewBox="0 0 12 12" fill="none" stroke="#fff" stroke-width="1.6"><circle cx="5" cy="5" r="3.5"/><line x1="7.6" y1="7.6" x2="10.5" y2="10.5"/></svg>
  </div>
</header>

<section class="hero">
  <div class="abs eyebrow">INNOVATING THE FUTURE OF HUMAN HEALTH</div>
  <h1 class="abs hero-title">BREAKTHROUGH BIOMEDICAL TECHNOLOGY<br>TRANSFORMING&nbsp; DIAGNOSTICS &amp; CARE</h1>
  <p class="abs hero-copy">Lorem ipsum dolor sit amet, consectetur adipiscing elit, sed do eiusmod tempor incididunt ut labore et dolore magna aliqua enim ad minim veniam.</p>
  <div class="abs btn btn-ghost" style="left:680px; top:254px; width:135px;">LEARN MORE</div>
  <div class="abs btn btn-grad dark-text" style="left:834px; top:254px; width:136px;">CONTACT US</div>
  <div class="abs hero-media" role="img" aria-label="Glowing illustration of a human head with brain and a magnified neuron"></div>
</section>

<section class="tech">
  <h2 class="abs section-title" style="top:858px;">TECHNOLOGY THAT <span>MAKES A DIFFERENCE</span></h2>

  <div class="abs feature" style="left:110px; top:939px;">
    <div class="icon-ring">
      <svg width="34" height="34" viewBox="0 0 34 34" fill="none" stroke="#fff" stroke-width="1.4"><rect x="4" y="6" width="26" height="18" rx="2"/><line x1="13" y1="29" x2="21" y2="29"/><line x1="17" y1="24" x2="17" y2="29"/><circle cx="15" cy="15" r="4"/><line x1="18" y1="18" x2="22" y2="22"/></svg>
    </div>
    <h3>DIAGNOSTIC PRECISION</h3>
    <p>Lorem ipsum dolor sit amet, consectetur adipiscing elit, sed do eiusmod tempor incididunt ut labore et</p>
  </div>
  <div class="abs feature" style="left:460px; top:939px;">
    <div class="icon-ring">
      <svg width="34" height="34" viewBox="0 0 34 34" fill="none" stroke="#fff" stroke-width="1.4"><rect x="5" y="20" width="4" height="9"/><rect x="12" y="15" width="4" height="14"/><rect x="19" y="11" width="4" height="18"/><rect x="26" y="7" width="4" height="22"/><polyline points="5,14 12,9 19,10 28,3"/></svg>
    </div>
    <h3>AI-POWERED ANALYTICS</h3>
    <p>Lorem ipsum dolor sit amet, consectetur adipiscing elit, sed do eiusmod tempor incididunt ut labore et</p>
  </div>
  <div class="abs feature" style="left:810px; top:939px;">
    <div class="icon-ring">
      <svg width="34" height="34" viewBox="0 0 34 34" fill="none" stroke="#fff" stroke-width="1.4"><rect x="4" y="8" width="22" height="16" rx="2"/><polyline points="7,18 11,14 15,17 21,11"/><circle cx="25" cy="24" r="5"/><circle cx="25" cy="24" r="1.6"/></svg>
    </div>
    <h3>REAL-TIME MONITORING</h3>
    <p>Lorem ipsum dolor sit amet, consectetur adipiscing elit, sed do eiusmod tempor incididunt ut labore et</p>
  </div>

  <div class="abs btn btn-grad" style="left:485px; top:1225px; width:230px; height:41px;">VIEW MORE TECHNOLOGIES</div>
</section>

<section class="about">
  <div class="abs about-box"></div>
  <h2 class="abs about-title">WHO WE <span>ARE</span></h2>
  <div class="abs about-copy">
    <p>Lorem ipsum dolor sit amet, consectetur adipiscing elit, sed do eiusmod tempor incididunt ut labore et dolore magna aliqua</p>
    <p>Lorem ipsum dolor sit amet, consectetur adipiscing elit, sed do eiusmod tempor incididunt ut labore et dolore magna aliqua. Ut enim ad minim veniam, quis nostrud exercitation ullamco laboris nisi ut aliquip ex ea commodo consequat.</p>
  </div>
  <div class="abs btn btn-ghost" style="left:170px; top:1807px; width:135px; height:41px;">LEARN MORE</div>
  <div class="abs about-media" role="img" aria-label="Close-up of cyan red blood cells flowing"></div>
</section>

<section class="why">
  <h2 class="abs section-title" style="top:2005px;">WHY CHOOSE <span>LUMORA</span></h2>

  <div class="abs why-item" style="top:2087px;">
    <h3>SCALABLE AND INTEGRATIVE WITH EXISTING SYSTEMS</h3>
    <p>Lorem ipsum dolor sit amet, consectetur adipiscing<br>elit, sed do eiusmod tempor</p>
  </div>

  <div class="abs orbit"></div>
  <div class="abs core"></div>

  <div class="abs node" style="left:567px; top:2219px;">
    <svg width="32" height="32" viewBox="0 0 32 32" fill="none" stroke="#fff" stroke-width="1.4"><circle cx="16" cy="16" r="5"/><circle cx="16" cy="16" r="10" stroke-dasharray="4 3"/></svg>
  </div>
  <div class="abs node" style="left:388px; top:2417px;">
    <svg width="32" height="32" viewBox="0 0 32 32" fill="none" stroke="#fff" stroke-width="1.4"><rect x="7" y="6" width="16" height="22" rx="2"/><rect x="12" y="3" width="6" height="5" rx="1"/><line x1="11" y1="14" x2="19" y2="14"/><line x1="11" y1="19" x2="16" y2="19"/><circle cx="23" cy="24" r="4"/></svg>
  </div>
  <div class="abs node" style="left:741px; top:2417px;">
    <svg width="32" height="32" viewBox="0 0 32 32" fill="none" stroke="#fff" stroke-width="1.4"><rect x="5" y="5" width="16" height="22" rx="2"/><line x1="9" y1="11" x2="17" y2="11"/><line x1="9" y1="16" x2="15" y2="16"/><circle cx="23" cy="20" r="5"/><polyline points="21,20 22.6,21.8 25.5,18.5"/></svg>
  </div>
  <div class="abs node" style="left:567px; top:2576px;">
    <svg width="32" height="32" viewBox="0 0 32 32" fill="none" stroke="#fff" stroke-width="1.4"><circle cx="16" cy="11" r="5"/><path d="M7 28c0-6 4-9 9-9s9 3 9 9"/><line x1="11" y1="8" x2="21" y2="8"/></svg>
  </div>

  <div class="abs side-item left" style="top:2377px;">
    <h3>PATENT-PENDING TECHNOLOGY</h3>
    <p>Lorem ipsum dolor sit amet, consectetur adipiscing elit, sed do eiusmod tempor incididunt</p>
  </div>
  <div class="abs side-item right" style="top:2377px;">
    <h3>PEER-REVIEWED VALIDATION</h3>
    <p>Lorem ipsum dolor sit amet, consectetur adipiscing elit, sed do eiusmod tempor incididunt</p>
  </div>

  <div class="abs why-item" style="top:2688px;">
    <h3>BACKED BY LEADING SCIENTISTS AND ENGINEERS</h3>
    <p>Lorem ipsum dolor sit amet, consectetur adipiscing<br>elit, sed do eiusmod tempor</p>
  </div>
</section>

<section class="news">
  <h2 class="abs section-title" style="top:2854px;">LATEST <span>DEVELOPMENTS</span></h2>

  <article class="abs card" style="left:119px;">
    <div class="media" role="img" aria-label="Pink and blue molecular structure" style="background:linear-gradient(135deg,#e8c9dd,#b9a6d8 50%,#d6e4f3);"></div>
    <div class="date">13TH APRIL 2025</div>
    <h3>PRODUCT LAUNCH NEWS</h3>
    <p>Lorem ipsum dolor sit amet, consectetur adipiscing</p>
  </article>
  <article class="abs card featured" style="left:446px;">
    <div class="media" role="img" aria-label="Patient wearing a forehead sensor during a clinical test" style="background:linear-gradient(135deg,#c9c4c1,#8a7b74 55%,#3a3a40);"></div>
    <div class="date">13TH APRIL 2025</div>
    <h3>CLINICAL STUDIES</h3>
    <p>Lorem ipsum dolor sit amet, consectetur adipiscing</p>
    <div class="corner">
      <svg width="12" height="12" viewBox="0 0 12 12" fill="none" stroke="#fff" stroke-width="1.8"><polyline points="4,2 8,6 4,10"/></svg>
    </div>
  </article>
  <article class="abs card" style="left:772px;">
    <div class="media" role="img" aria-label="Laboratory sample tubes and gloved hand" style="background:linear-gradient(135deg,#3b6fd0,#9fc0ee 55%,#e7eef8);"></div>
    <div class="date">13TH APRIL 2025</div>
    <h3>PRESS RELEASES</h3>
    <p>Lorem ipsum dolor sit amet, consectetur adipiscing</p>
  </article>

  <div class="abs btn btn-grad" style="left:514px; top:3398px; width:170px; height:41px;">VIEW MORE NEWS</div>
</section>

<footer>
  <div class="abs footer"></div>
  <div class="abs brand footer-brand">
    <div class="brand-dot" style="width:58px; height:58px;"></div>
    <div class="brand-name" style="font-size:44px;">LUMORA</div>
  </div>
  <nav class="abs footer-nav">
    <span>HOME</span><span class="sep">|</span>
    <span>ABOUT</span><span class="sep">|</span>
    <span>TECHNOLOGY</span><span class="sep">|</span>
    <span>PRESS</span><span class="sep">|</span>
    <span>CONTACT US</span>
  </nav>
  <div class="abs copyright">@<span>LUMORA</span> 2025 COPYRIGHTS &nbsp;&nbsp;&nbsp;&nbsp;|&nbsp;&nbsp;&nbsp;&nbsp; ALL RIGHTS RESERVED</div>
</footer>

</body>
</html>
```